New Business Card for Web Design/Internet Marketing Company

Looking for a great looking new business card. We are a 10 year old web design, internet marketing and website management company that works mostly with small businesses.

Our new card needs to better match the colors and style of our website, be bold, extremely usable and slightly edgy.

Target Market(s)

Small/Medium businesses that have websites

Industry/Entity Type

Internet

Requirements
Must have
• Front and back design, full color, rounded corners please

Must use the colors/style of our website (JPG provided)

INFO FOR CARDS (as readable as possible please)
Mark Lenner
President/CEO
mark@trelvanmedia.example
Phone: 520-381-7459
Toll Free: 866-381-7459
Address: 4315 W. Calloway Ave. Ste. 140, Tucson, AZ 85792

THINGS I WANT TO PROMOTE (if there is room):
1. Our Website - www.trelvanmedia.example

2. Social Media
Twitter: @trelvanmedia
Facebook: www.facebook.com/trelvanmedia

3. Our Services
Web Design
Internet Marketing
Website Management

```html
<!DOCTYPE html>
<html lang="en">
<head>
<meta charset="utf-8">
<title>Trelvan Media – Business Card, Front and Back</title>
<link rel="stylesheet" href="https://fonts.googleapis.com/css2?family=Open+Sans:wght@400;600;700&display=swap">
<style>
  :root {
    --backdrop: #8a5d3b;
    --card-white: #ffffff;
    --brand-blue: #1b8ec8;
    --brand-orange: #f0822f;
    --text-grey: #555a5e;
    --services-heading: #4f4640;
    --divider: #c9ced2;
  }
  * { box-sizing: border-box; margin: 0; padding: 0; }
  html, body {
    width: 1200px;
    height: 402px;
    overflow: hidden;
    background: var(--backdrop);
    font-family: "Open Sans", Arial, sans-serif;
  }
  .stage {
    position: relative;
    width: 1200px;
    height: 402px;
  }
  .card {
    position: absolute;
    top: 54px;
    width: 511px;
    height: 296px;
    overflow: hidden;
  }
  .card--front { left: 63px; background: var(--card-white); }
  .card--back { left: 627px; background: var(--brand-orange); }

  /* Front */
  .front-wave { position: absolute; inset: 0; }
  .brand-mark {
    position: absolute;
    left: 34px;
    top: 128px;
    display: flex;
    align-items: center;
    gap: 10px;
  }
  .brand-mark__dot {
    width: 20px;
    height: 20px;
    border-radius: 50%;
    background: var(--brand-orange);
  }
  .brand-mark__name {
    font-size: 31px;
    font-weight: 700;
    color: var(--brand-blue);
    letter-spacing: -0.5px;
  }
  .divider {
    position: absolute;
    left: 292px;
    top: 86px;
    width: 1px;
    height: 130px;
    background: var(--divider);
  }
  .identity {
    position: absolute;
    left: 304px;
    top: 50px;
    color: var(--brand-blue);
  }
  .identity__name { font-size: 18px; font-weight: 600; line-height: 22px; }
  .identity__title { font-size: 12px; line-height: 16px; }
  .contact-list {
    position: absolute;
    left: 306px;
    top: 108px;
    list-style: none;
    color: var(--text-grey);
    font-size: 12.2px;
    line-height: 17.6px;
  }
  .contact-list li { display: flex; align-items: center; gap: 5px; }
  .contact-icon { width: 9px; height: 9px; flex: none; }
  .address {
    position: absolute;
    right: 18px;
    bottom: 8px;
    color: var(--card-white);
    font-size: 11px;
  }

  /* Back */
  .back-mark {
    position: absolute;
    left: 0;
    right: 0;
    top: 76px;
    display: flex;
    justify-content: center;
    align-items: center;
    gap: 12px;
  }
  .back-mark__dot {
    width: 26px;
    height: 26px;
    border-radius: 50%;
    background: var(--brand-blue);
  }
  .back-mark__name {
    font-size: 40px;
    font-weight: 700;
    color: var(--card-white);
    letter-spacing: -0.5px;
  }
  .services {
    position: absolute;
    left: 0;
    right: 0;
    top: 168px;
    text-align: center;
  }
  .services__heading {
    display: inline-block;
    font-size: 20px;
    font-weight: 600;
    color: var(--services-heading);
    padding: 0 14px 1px;
    border-bottom: 2px solid var(--card-white);
  }
  .services__list {
    margin-top: 12px;
    color: var(--card-white);
    font-size: 17px;
    line-height: 26px;
  }
</style>
</head>
<body>
<main class="stage">

  <section class="card card--front" aria-label="Business card front">
    <svg class="front-wave" viewBox="0 0 511 296" width="511" height="296" aria-hidden="true">
      <path d="M0 262 C150 232 330 222 511 244" fill="none" stroke="var(--brand-orange)" stroke-width="5"/>
      <path d="M0 268 C150 244 330 232 511 252 L511 296 L0 296 Z" fill="var(--brand-blue)"/>
    </svg>

    <div class="brand-mark">
      <span class="brand-mark__dot"></span>
      <span class="brand-mark__name">Trelvan Media</span>
    </div>

    <div class="identity">
      <p class="identity__name">Mark Lenner</p>
      <p class="identity__title">President/CEO</p>
    </div>

    <span class="divider"></span>

    <ul class="contact-list">
      <li><svg class="contact-icon" viewBox="0 0 10 10"><circle cx="5" cy="5" r="4.3" fill="none" stroke="var(--brand-blue)" stroke-width="1.4"/></svg>520-381-7459</li>
      <li><svg class="contact-icon" viewBox="0 0 10 10"><path d="M2 1 L4 1 L4.6 3.2 L3.4 4.2 Q4.6 6 6 6.8 L7 5.6 L9 6.2 L9 8.2 Q5 9 1.6 4.6 Q1 2.6 2 1 Z" fill="var(--brand-blue)"/></svg>866-381-7459</li>
      <li><svg class="contact-icon" viewBox="0 0 10 10"><rect x="0.5" y="2" width="9" height="6.5" fill="var(--brand-blue)"/><path d="M0.5 2 L5 5.6 L9.5 2" fill="none" stroke="#fff" stroke-width="1"/></svg>mark@trelvanmedia.example</li>
      <li><svg class="contact-icon" viewBox="0 0 10 10"><circle cx="5" cy="5" r="4.3" fill="none" stroke="var(--brand-blue)" stroke-width="1.2"/><path d="M0.7 5 H9.3 M5 0.7 V9.3" stroke="var(--brand-blue)" stroke-width="1"/></svg>www.trelvanmedia.example</li>
      <li><svg class="contact-icon" viewBox="0 0 10 10"><rect x="0.5" y="0.5" width="9" height="9" rx="1.5" fill="var(--brand-blue)"/></svg>trelvanmedia</li>
      <li><svg class="contact-icon" viewBox="0 0 10 10"><rect x="0.5" y="0.5" width="9" height="9" rx="1.5" fill="var(--brand-blue)"/></svg>@trelvanmedia</li>
    </ul>

    <p class="address">4315 W. Calloway Ave. Ste. 140, Tucson, AZ 85792</p>
  </section>

  <section class="card card--back" aria-label="Business card back">
    <div class="back-mark">
      <span class="back-mark__dot"></span>
      <span class="back-mark__name">Trelvan Media</span>
    </div>
    <div class="services">
      <h2 class="services__heading">Our Services</h2>
      <p class="services__list">Web Design &nbsp;•&nbsp; Internet Marketing<br>Website Management</p>
    </div>
  </section>

</main>
</body>
</html>
```